logo & Business Card Design

BrightHaven Termite & Pest Control, I need a great logo, take my ideas and run with them!
I will use this in marketing and website so needs to be eye catching but professional

Target Market(s)

Resedintial & Business

Industry/Entity Type

Marketing

Contact Information for Business Card

Need front side with pertinent info & Logo; back side will have a 25% off initial services Coupon!

Font styles to use
Sans Serif

Colors
ec1f27
1b1b1b

Requirements
Must have
• Professional logo and style
Nice to have
• Raised lettering, black, red, white colors maybe? I'm flexible, but those colors go good on any background, vehicle, uniform, etc...
Should not have
• Cheesy

```html
<!DOCTYPE html>
<html lang="en">
<head>
<meta charset="utf-8">
<title>BrightHaven Termite &amp; Pest Control — Business Card</title>
<link href="https://fonts.googleapis.com/css2?family=Open+Sans:wght@400;600&display=swap" rel="stylesheet">
<style>
  :root {
    --backdrop: #2a2724;
    --card: #161616;
    --card-edge: #0c0c0c;
    --silver: #d6d6d6;
    --white: #f2f2f2;
    --divider: #4a4a4a;
    --icon-ink: #161616;
  }
  * { margin: 0; padding: 0; box-sizing: border-box; }
  html, body {
    width: 1200px;
    height: 844px;
    overflow: hidden;
    background: var(--backdrop);
    font-family: "Open Sans", sans-serif;
  }
  .stage {
    position: relative;
    width: 1200px;
    height: 844px;
    display: flex;
    align-items: center;
    justify-content: center;
    gap: 60px;
  }
  .card {
    position: relative;
    width: 520px;
    height: 300px;
    background: var(--card);
    border: 1px solid var(--card-edge);
    border-radius: 4px;
    box-shadow: 0 10px 30px rgba(0,0,0,0.45);
    color: var(--white);
  }
  .brand {
    position: absolute;
    left: 50%;
    transform: translateX(-50%);
    display: flex;
    align-items: center;
    gap: 10px;
    white-space: nowrap;
    color: var(--silver);
    font-weight: 600;
  }
  .brand-mark {
    background: var(--silver);
    flex: none;
  }
  .card-front .brand { top: 52px; font-size: 15px; }
  .card-front .brand-mark { width: 16px; height: 16px; }
  .card-back .brand { top: 104px; font-size: 19px; }
  .card-back .brand-mark { width: 20px; height: 20px; }
  .identity {
    position: absolute;
    right: 252px;
    top: 150px;
    text-align: right;
  }
  .identity .person-name { font-size: 23px; font-weight: 400; line-height: 1.2; }
  .identity .person-role { font-size: 14px; color: var(--silver); margin-bottom: 6px; }
  .identity .address { font-size: 15px; line-height: 1.35; }
  .divider {
    position: absolute;
    left: 284px;
    top: 140px;
    width: 1px;
    height: 112px;
    background: var(--divider);
  }
  .contacts {
    position: absolute;
    left: 300px;
    top: 142px;
    list-style: none;
  }
  .contacts li {
    display: flex;
    align-items: center;
    gap: 10px;
    font-size: 14px;
    height: 26px;
    white-space: nowrap;
  }
  .contacts svg { width: 16px; height: 16px; flex: none; }
  .tagline {
    position: absolute;
    left: 0;
    right: 0;
    top: 178px;
    text-align: center;
    font-size: 12px;
    color: var(--silver);
  }
</style>
</head>
<body>
<main class="stage">
  <section class="card card-front" aria-label="Business card front">
    <div class="brand"><span class="brand-mark"></span>BrightHaven Termite &amp; Pest Control</div>
    <div class="identity">
      <p class="person-name">John Smith</p>
      <p class="person-role">Managing Director</p>
      <p class="address">12345, Address Goes Here<br>Country Name, 123456</p>
    </div>
    <div class="divider"></div>
    <ul class="contacts">
      <li>
        <svg viewBox="0 0 16 16" aria-hidden="true"><rect width="16" height="16" rx="3" fill="#f2f2f2"/><path d="M5 4h2l1 2.5-1.2 1a6 6 0 0 0 2.7 2.7l1-1.2L13 10v2a1 1 0 0 1-1 1A9 9 0 0 1 4 5a1 1 0 0 1 1-1z" fill="#161616"/></svg>
        (044)-456-7890
      </li>
      <li>
        <svg viewBox="0 0 16 16" aria-hidden="true"><rect width="16" height="16" rx="3" fill="#f2f2f2"/><rect x="5" y="3" width="6" height="10" rx="1" fill="#161616"/><rect x="6" y="4.5" width="4" height="6" fill="#f2f2f2"/></svg>
        123-456-7890
      </li>
      <li>
        <svg viewBox="0 0 16 16" aria-hidden="true"><rect width="16" height="16" rx="3" fill="#f2f2f2"/><rect x="3" y="4.5" width="10" height="7" fill="#161616"/><path d="M3.5 5l4.5 3.5L12.5 5" stroke="#f2f2f2" fill="none"/></svg>
        info@youremail.com
      </li>
      <li>
        <svg viewBox="0 0 16 16" aria-hidden="true"><rect width="16" height="16" rx="3" fill="#f2f2f2"/><path d="M6.5 9.5l3-3M7 5.5l1-1a2 2 0 0 1 3 3l-1 1M9 10.5l-1 1a2 2 0 0 1-3-3l1-1" stroke="#161616" stroke-width="1.4" fill="none" stroke-linecap="round"/></svg>
        www.website.com
      </li>
    </ul>
  </section>

  <section class="card card-back" aria-label="Business card back">
    <div class="brand"><span class="brand-mark"></span>BrightHaven Termite &amp; Pest Control</div>
    <p class="tagline">“A Shield of protection For Your Home or Business”</p>
  </section>
</main>
</body>
</html>
```